Website Design for Employee Moral and Happiness Company

Looking for a clean website design that explains our features in a step by step manner so our visitors know exactly what our site does before logging in.

The site is called "Velrato". See logo design and video for a sample of style and an overview of what we do.

Target Market(s)

Business owners that are looking to retain employees.

Number of Pages Required

1 page

```html
<!DOCTYPE html>
<html lang="en">
<head>
<meta charset="UTF-8">
<title>Velrato — Workplace Happiness</title>
<link href="https://fonts.googleapis.com/css2?family=Crimson+Pro:wght@700&family=Nunito:wght@400;600;700&display=swap" rel="stylesheet">
<style>
  :root {
    --bg: #e8dfd6;
    --ink: #2f2c2a;
    --body: #55504c;
    --accent: #ff6a00;
    --rule: #f3ede7;
    --navy: #0a1b2b;
    --blue: #234d7d;
    --teal: #2ba4b2;
    --desk: #efe7de;
    --dot: #6b6561;
  }
  * { box-sizing: border-box; margin: 0; padding: 0; }
  html, body { width: 1200px; height: 698px; overflow: hidden; }
  body {
    position: relative;
    background: var(--bg);
    font-family: "Nunito", sans-serif;
    color: var(--ink);
  }
  .site-header {
    position: absolute; left: 0; top: 0; width: 1200px; height: 89px;
    border-bottom: 2px solid var(--rule);
  }
  .brand {
    position: absolute; left: 66px; top: 16px;
    font-family: "Crimson Pro", serif; font-weight: 700; font-size: 48px;
    line-height: 52px; color: var(--ink);
  }
  .main-nav a {
    position: absolute; top: 34px; font-size: 15.5px; line-height: 20px;
    color: var(--ink); text-decoration: none;
  }
  .main-nav a.is-active { color: var(--accent); border-bottom: 1px solid var(--accent); }
  .login {
    position: absolute; left: 906px; top: 34px; font-size: 15.5px; line-height: 20px;
    display: flex; align-items: center; gap: 9px; color: var(--ink);
  }
  .btn {
    position: absolute; display: flex; align-items: center; justify-content: center;
    font-weight: 700; text-transform: uppercase; border-radius: 999px; font-size: 16px;
    letter-spacing: 0.2px;
  }
  .btn-primary { background: var(--accent); color: #fff; }
  .btn-outline { border: 2px solid var(--accent); color: var(--accent); gap: 30px; }
  .header-signup { left: 995px; top: 18px; width: 140px; height: 45px; }
  .hero-title {
    position: absolute; left: 66px; top: 205px; width: 460px;
    font-family: "Crimson Pro", serif; font-weight: 700; font-size: 41px;
    line-height: 44px; color: var(--ink);
  }
  .hero-text {
    position: absolute; left: 65px; top: 361px; width: 430px;
    font-size: 17px; line-height: 30px; color: var(--body);
  }
  .hero-signup { left: 67px; top: 527px; width: 244px; height: 52px; }
  .hero-more { left: 339px; top: 527px; width: 245px; height: 52px; }
  .hero-art {
    position: absolute; left: 548px; top: 197px; width: 600px; height: 320px;
    border-radius: 190px 40px 14px 14px;
    background: linear-gradient(120deg, var(--navy) 0%, var(--blue) 30%, var(--teal) 62%, var(--desk) 100%);
  }
  .section-dots { position: absolute; left: 1168px; top: 266px; width: 14px; height: 262px; }
  .section-dots .track { position: absolute; left: 6px; top: 8px; width: 2px; height: 246px; background: var(--dot); }
  .section-dots .dot {
    position: absolute; left: 1px; width: 12px; height: 12px; border-radius: 50%;
    border: 1.5px solid var(--dot); background: var(--bg);
  }
  .section-dots .dot.is-current {
    left: -4px; width: 22px; height: 22px; background: var(--ink);
    border: 4px solid #8d8884;
  }
  .dots-label {
    position: absolute; left: 1118px; top: 266px; font-size: 12px; font-weight: 700; color: var(--ink);
  }
</style>
</head>
<body>
  <header class="site-header">
    <div class="brand">Velrato</div>
    <nav class="main-nav">
      <a class="is-active" style="left:278px">Home</a>
      <a style="left:342px">Boring Work Events</a>
      <a style="left:499px">Introducing Velrato</a>
      <a style="left:654px">Why Velrato</a>
      <a style="left:767px">Testimonials</a>
    </nav>
    <div class="login">
      <svg width="13" height="13" viewBox="0 0 13 13" fill="none" stroke="currentColor" stroke-width="1.3">
        <path d="M1 6.5h7M5.5 4l2.5 2.5L5.5 9M9 1.5h3v10H9"/>
      </svg>
      Login
    </div>
    <a class="btn btn-primary header-signup">Sign up</a>
  </header>

  <main>
    <h1 class="hero-title">Boost your employee’s workplace happiness, moral &amp; work retention</h1>
    <p class="hero-text">Lorem ipsum dolor sit amet, consectetur adipiscing elit, sed do eiusmod tempor incididunt ut labore et dolore magna aliqua. Quis ipsum suspendisse ultrices gravida. Risus commodo facilisis.</p>
    <a class="btn btn-primary hero-signup">Sign up</a>
    <a class="btn btn-outline hero-more">More details
      <svg width="14" height="12" viewBox="0 0 14 12" fill="none" stroke="currentColor" stroke-width="1.8"><path d="M1 6h11M7.5 1.5 12 6l-4.5 4.5"/></svg>
    </a>

    <div class="hero-art" role="img" aria-label="Illustration of an employee working on a laptop at his desk in front of a round window, with floating calendar, mail, clock and chat icons"></div>

    <div class="dots-label">Home</div>
    <div class="section-dots" aria-label="Section navigation">
      <span class="track"></span>
      <span class="dot is-current" style="top:-4px"></span>
      <span class="dot" style="top:42px"></span>
      <span class="dot" style="top:83px"></span>
      <span class="dot" style="top:125px"></span>
      <span class="dot" style="top:166px"></span>
      <span class="dot" style="top:207px"></span>
      <span class="dot" style="top:248px"></span>
    </div>
  </main>
</body>
</html>
```